Professional, modern and unique business card. We are looking to present a new look to our business cards however we don't want to divert too far away from original template. We want social media links and our 3 office addresses on the backside of the business cards. Please see attached business card templates for ideas.
Crestline Homes Color Code:
R: 7
G:63
B:86

Target Market(s)

Real Estate

Industry/Entity Type

Real Estate

Contact Information for Business Card

Follow the attached templates. In need of a more modern and unique touch but don't want to divert from the original theme or color.
Crestline Homes Color Code:
R: 7
G:63
B:86

Font styles to use
Serif

Requirements
Must have
• Crestline Homes logo, Crestline homes colors, social media links, 3 office addresses,
Nice to have
• information about Crestline Homes and QR codes. You can check out www.mycrestlinehomes.example

```html
<!DOCTYPE html>
<html lang="en">
<head>
<meta charset="utf-8">
<title>Crestline Homes – Business Card</title>
<link href="https://fonts.googleapis.com/css2?family=Lato:wght@400;700&display=swap" rel="stylesheet">
<style>
  :root {
    --backdrop: #3b3532;
    --card: #073f56;
    --ink: #ffffff;
    --ink-soft: #d7e3ea;
    --rule: rgba(255,255,255,0.35);
    --dot-blue: #3f6fb0;
    --dot-red: #d9323c;
    --dot-sky: #2d9ad6;
    --dot-grey: #6f8ea3;
  }
  * { box-sizing: border-box; margin: 0; padding: 0; }
  html, body {
    width: 1200px; height: 844px; overflow: hidden;
    background: var(--backdrop);
    font-family: "Lato", Arial, sans-serif;
    color: var(--ink);
  }
  .stage { position: relative; width: 1200px; height: 844px; }
  .card {
    position: absolute; width: 540px; height: 309px;
    background: var(--card);
    box-shadow: 0 14px 30px rgba(0,0,0,0.45);
  }
  .card--front { left: 40px; top: 268px; }
  .card--back { left: 620px; top: 268px; }

  /* Front */
  .brand {
    position: absolute; right: 48px; top: 46px;
    display: flex; align-items: center; gap: 10px;
  }
  .brand__mark { width: 18px; height: 18px; border-radius: 50%; background: var(--ink-soft); }
  .brand__name { font-size: 30px; font-weight: 700; color: var(--ink-soft); letter-spacing: 1px; }
  .card--front .rule-top {
    position: absolute; left: 0; right: 40px; top: 128px;
    height: 1px; background: var(--rule);
  }
  .person { position: absolute; left: 40px; top: 178px; }
  .person__name { font-size: 19px; font-weight: 700; letter-spacing: 0.5px; }
  .person__title { font-size: 13px; color: var(--ink-soft); margin-top: 2px; }
  .card--front .rule-bottom {
    position: absolute; left: 40px; right: 40px; top: 232px;
    height: 1px; background: var(--rule);
  }
  .contact {
    position: absolute; left: 40px; top: 244px;
    font-size: 12.5px; line-height: 1.55;
  }
  .contact span + span { margin-left: 14px; }

  /* Back */
  .socials {
    position: absolute; left: 40px; right: 40px; top: 40px;
    display: grid; grid-template-columns: 1fr 1fr; column-gap: 30px;
  }
  .socials ul { list-style: none; }
  .socials li {
    display: flex; align-items: center; gap: 7px;
    font-size: 12.5px; line-height: 1; margin-bottom: 8px;
  }
  .socials .col-left { padding-top: 56px; }
  .dot { width: 14px; height: 14px; border-radius: 50%; flex: none; }
  .dot--blue { background: var(--dot-blue); }
  .dot--red { background: var(--dot-red); }
  .dot--sky { background: var(--dot-sky); }
  .dot--grey { background: var(--dot-grey); }
  .card--back .rule-top {
    position: absolute; left: 290px; right: 40px; top: 80px;
    height: 1px; background: var(--rule);
  }
  .card--back .rule-mid {
    position: absolute; left: 40px; right: 40px; top: 196px;
    height: 1px; background: var(--rule);
  }
  .offices {
    position: absolute; left: 40px; right: 40px; top: 214px;
    display: flex; font-size: 12.5px; line-height: 1.4;
  }
  .office { padding: 0 12px; border-left: 1px solid var(--rule); }
  .office:first-child { padding-left: 0; border-left: none; }
</style>
</head>
<body>
<main class="stage">

  <section class="card card--front" aria-label="Card front">
    <div class="brand">
      <span class="brand__mark"></span>
      <span class="brand__name">Crestline Homes</span>
    </div>
    <div class="rule-top"></div>
    <div class="person">
      <p class="person__name">DANIEL REYES</p>
      <p class="person__title">Managing Director</p>
    </div>
    <div class="rule-bottom"></div>
    <div class="contact">
      <p><span>T:(044) 555 010 200</span><span>F:(044) 555010201</span><span>M:(044)555010202</span></p>
      <p><span>E:info@crestlinehomes.example</span><span>www.mycrestlinehomes.example</span></p>
    </div>
  </section>

  <section class="card card--back" aria-label="Card back">
    <div class="socials">
      <ul class="col-left">
        <li><span class="dot dot--blue"></span>CrestlinehomesNY</li>
        <li><span class="dot dot--red"></span>Info at Crestline Homes</li>
        <li><span class="dot dot--sky"></span>Crestline Homes New York</li>
      </ul>
      <ul class="col-right">
        <li><span class="dot dot--red"></span>Crestline Homes</li>
        <li><span class="dot dot--sky"></span>@CrestlineHomesQ</li>
        <li><span class="dot dot--grey"></span>@CrestlineHomesNY</li>
      </ul>
    </div>
    <div class="rule-top"></div>
    <div class="rule-mid"></div>
    <div class="offices">
      <p class="office">418-20 Harbor Blvd<br>Bay Point, NY 11350</p>
      <p class="office">72-40 Maple Blvd<br>Elm Garden, NY 11420</p>
      <p class="office">905 Union Ave<br>Brookdale, NY 11230</p>
    </div>
  </section>

</main>
</body>
</html>
```